Health Care Company with Logo Needs Business Cards designed

We are a luxury behavioral health company looking for business cards design we already have a logo and are looking for someone to design a sophisticated luxurious looking business card. Please note that Card design should be captivating just like the logo and also encompass the logo color

Industry/Entity Type

Healthcare

Contact Information for Business Card

Logo,company name, tagline, my name and title, contact details, and physical address

```html
<!DOCTYPE html>
<html lang="en">
<head>
<meta charset="utf-8">
<title>Corvane Behavioral Health – Business Cards</title>
<link rel="stylesheet" href="https://fonts.googleapis.com/css2?family=Oswald:wght@500&family=Roboto+Condensed:wght@700&family=Roboto:wght@400&display=swap">
<style>
  :root {
    --bg: #262626;
    --paper: #ffffff;
    --purple: #7f3f98;
    --cyan: #0ba8e6;
    --ink: #1e1e1e;
    --rule: #b5b5b5;
  }
  * { margin: 0; padding: 0; box-sizing: border-box; }
  html, body { width: 1065px; height: 1200px; overflow: hidden; background: var(--bg); }
  .stage { position: relative; width: 1065px; height: 1200px; }

  .card { position: absolute; width: 583px; height: 363px; overflow: hidden; box-shadow: 3px 4px 6px rgba(0,0,0,0.6); }

  /* Front */
  .card--front {
    left: 292px; top: 218px;
    background: var(--paper);
    border-radius: 0 181px 181px 0;
  }
  .card--front .sheen {
    position: absolute; inset: 0;
    background: linear-gradient(180deg, rgba(255,255,255,0) 25%, rgba(0,0,0,0.09) 100%);
    clip-path: polygon(78% 14%, 100% 14%, 100% 100%, 52% 100%);
  }
  .brand-vertical {
    position: absolute; left: 133px; top: 57px; height: 246px;
    display: flex; flex-direction: column; justify-content: center; align-items: center;
    writing-mode: vertical-rl; transform: rotate(180deg);
  }
  .brand-vertical .brand-name {
    font: 700 24px/1 "Roboto Condensed", sans-serif; color: var(--purple); white-space: nowrap;
  }
  .brand-vertical .brand-tagline {
    margin-left: 6px;
    font: 700 7.5px/1 "Roboto Condensed", sans-serif; color: var(--cyan);
    letter-spacing: 2.4px; white-space: nowrap;
  }
  .brand-mark { position: absolute; left: 74px; top: 156px; width: 44px; height: 44px; background: var(--purple); }
  .divider { position: absolute; left: 201px; top: 95px; width: 1px; height: 173px; background: var(--rule); }

  .details { position: absolute; left: 226px; top: 88px; color: var(--ink); }
  .person-name { font: 500 30px/1 Oswald, sans-serif; color: var(--purple); letter-spacing: -0.5px; }
  .person-title { font: 400 18px/1 Roboto, sans-serif; color: var(--cyan); margin-top: 1px; }
  .contact-list { list-style: none; margin-top: 16px; }
  .contact-list li { display: flex; align-items: center; font: 400 17px/21px Roboto, sans-serif; }
  .contact-list svg { width: 15px; height: 15px; margin-right: 6px; fill: var(--purple); flex: none; }
  .contact-list .accent { color: var(--purple); }
  .address { margin-top: 13px; font: 400 17px/21px Roboto, sans-serif; }

  /* Back */
  .card--back {
    left: 263px; top: 623px;
    border-radius: 181px 0 0 181px;
    background: linear-gradient(200deg, var(--cyan) 0%, #4a6fc2 40%, #7b45a0 70%, var(--purple) 100%);
  }
  .brand-lockup { position: absolute; left: 101px; top: 152px; display: flex; align-items: center; }
  .brand-lockup .brand-square { width: 42px; height: 42px; background: #fff; margin-right: 36px; }
  .brand-lockup .brand-name { font: 700 30px/1 "Roboto Condensed", sans-serif; color: #fff; white-space: nowrap; }
  .brand-lockup .brand-tagline { font: 700 10px/1 "Roboto Condensed", sans-serif; color: #fff; letter-spacing: 2.9px; margin-top: 7px; white-space: nowrap; }
</style>
</head>
<body>
<main class="stage">

  <section class="card card--front" aria-label="Business card front">
    <div class="sheen"></div>
    <div class="brand-mark"></div>
    <div class="brand-vertical">
      <span class="brand-name">Corvane Behavioral Health</span>
      <span class="brand-tagline">COMMITTED TO CALM, COMFORT AND RENEWAL</span>
    </div>
    <div class="divider"></div>
    <div class="details">
      <h1 class="person-name">Marcus Ellery</h1>
      <p class="person-title">Managing Director</p>
      <ul class="contact-list">
        <li><svg viewBox="0 0 24 24" aria-hidden="true"><path d="M6.6 10.8a15 15 0 0 0 6.6 6.6l2.2-2.2a1 1 0 0 1 1-.25 11.4 11.4 0 0 0 3.6.57 1 1 0 0 1 1 1V20a1 1 0 0 1-1 1A17 17 0 0 1 3 4a1 1 0 0 1 1-1h3.5a1 1 0 0 1 1 1c0 1.25.2 2.45.57 3.6a1 1 0 0 1-.25 1z"/></svg>044-987 654 321</li>
        <li><svg viewBox="0 0 24 24" aria-hidden="true"><path d="M2 5h20v14H2z M2 5l10 8 10-8" fill="var(--purple)" stroke="#fff" stroke-width="1.2"/></svg>hello@corvanehealth.com</li>
        <li><svg viewBox="0 0 24 24" aria-hidden="true"><path d="M12 2a10 10 0 1 0 0 20 10 10 0 0 0 0-20zm0 1.8c1.2 1.3 2 3.3 2.3 5.7H9.7C10 7.1 10.8 5.1 12 3.8zM4 11h3.9c0 .7 0 1.3.1 2H4a8 8 0 0 1 0-2zm.6 4h3.6c.4 1.8 1 3.3 1.9 4.5A8 8 0 0 1 4.6 15zm4-6.5H4.6a8 8 0 0 1 5.5-4.9c-.8 1.3-1.4 3-1.5 4.9zM12 20.2c-1.2-1.3-2-3.2-2.3-5.2h4.6c-.3 2-1.1 3.9-2.3 5.2zM9.6 13a15 15 0 0 1 0-2h4.8a15 15 0 0 1 0 2zm4.3 6.5c.9-1.2 1.5-2.7 1.9-4.5h3.6a8 8 0 0 1-5.5 4.5zm2.2-6.5c.1-.7.1-1.3.1-2H20a8 8 0 0 1 0 2zm-.7-4.5c-.1-1.9-.7-3.6-1.5-4.9a8 8 0 0 1 5.5 4.9z"/></svg>www.<span class="accent">corvanehealth</span>.com</li>
      </ul>
      <p class="address">17, Linden Park Avenue<br>30218, Northland</p>
    </div>
  </section>

  <section class="card card--back" aria-label="Business card back">
    <div class="brand-lockup">
      <div class="brand-square"></div>
      <div>
        <p class="brand-name">Corvane Behavioral Health</p>
        <p class="brand-tagline">COMMITTED TO CALM, COMFORT AND RENEWAL</p>
      </div>
    </div>
  </section>

</main>
</body>
</html>
```